VELMA, an e-commerce website with a twist, providing consumer-to-consumer and business-to-consumer sa

I have only uploaded 10 wire-frame pages of the website. These pages have been chosen for the different lay-outs and should give an idea of what will be needed. There are many more that I won’t upload yet, I aim to choose a winner first then there will be a high possibility that the winner will get the chance to do the design work for these later.
The design I have in mind is to keep it clean and easy with no/minimal fancy fonts and hieroglyphics. The logo is white with an orange highlight on a solid background of black, please note that the logo is white on a black background and is not a black box with white lettering, trust that makes sense. I like the idea of the top part of the website being black all the way across. I don’t see the need for more than 3 colours in the actual base website (the pictures and adverts added by users will add other colours). Although orange is the highlight colour in the logo I am open to suggestions on this, so long as the highlight colour features throughout the site.

Website width is 1220px, all pages in the PDF are 1220px

Logo font is Rezlong

The company is going to be like tradu, but much more focused on raising money for charity and humanitarian relief.

Target Market(s)

the modern era of smartphones and the sharing community

Industry/Entity Type

Business

Number of Pages Required

5+ page

Font styles to use
Sans Serif
Other font styles liked:
• rezlong

Colors
faa54b
f78f20
ffffff
000000
fbfbfb
f5f5f5

Requirements
Nice to have
• Although orange is the highlight colour in the logo I am open to suggestions on this, so long as the highlight colour features throughout the site.

```html
<!DOCTYPE html>
<html lang="en">
<head>
<meta charset="utf-8">
<title>Velma – Home</title>
<link rel="stylesheet" href="https://fonts.googleapis.com/css2?family=Comfortaa:wght@500;700&family=Open+Sans:ital,wght@0,400;0,600;0,700;1,400&family=Raleway:wght@500;600&display=swap">
<style>
:root{
  --black:#000000;
  --white:#ffffff;
  --orange:#f78f20;
  --orange-light:#faa54b;
  --off:#fbfbfb;
  --grey-bg:#f5f5f5;
  --text:#333333;
  --muted:#666666;
  --frame:#e3d9c9;
}
*{box-sizing:border-box;margin:0;padding:0}
html,body{width:1200px;height:2381px;overflow:hidden}
body{position:relative;background:var(--white);font-family:"Open Sans",Arial,sans-serif;color:var(--text)}
.abs{position:absolute}
svg.ico{width:14px;height:14px;fill:currentColor;vertical-align:-2px;margin-right:6px}

/* top bar */
.topbar{left:0;top:0;width:1200px;height:40px;background:var(--black);color:var(--white);font-size:14px}
.topbar .links{left:22px;top:10px;display:flex;gap:10px}
.topbar .right{left:498px;top:10px;display:flex;gap:10px}
.topbar .sep{color:#999}
.topbar .search{left:890px;top:0;width:310px;height:40px;background:#222;padding:11px 20px;display:flex;justify-content:space-between;font-size:15px}

/* header */
.header{left:0;top:40px;width:1200px;height:87px;background:var(--black);color:var(--white)}
.logo{left:24px;top:16px;font-family:"Comfortaa",sans-serif;font-weight:700;font-size:46px;letter-spacing:-1px;line-height:1}
.mainnav{right:20px;top:30px;display:flex;gap:16px;font-family:"Raleway",sans-serif;font-weight:600;font-size:17px}
.mainnav .sep{color:#bbb}

.heading{font-family:"Comfortaa",sans-serif;font-weight:700;color:var(--black)}
.small-head{font-size:20px}

/* videos */
.video{left:24px;width:273px;height:180px;border:1px solid #ddd;box-shadow:0 1px 4px rgba(0,0,0,.25);overflow:hidden;background:var(--white)}
.video .still{position:absolute;inset:6px 6px 16px 6px}
.video .bar{position:absolute;left:6px;right:6px;bottom:6px;height:10px;background:#222}
.video .bar i{position:absolute;left:0;top:0;height:3px;width:100%;background:#c00}
.video .play{position:absolute;left:50%;top:45%;transform:translate(-50%,-50%);width:54px;height:54px;border-radius:50%;background:rgba(0,0,0,.8)}
.video .play svg{position:absolute;left:19px;top:15px;width:22px;height:24px;fill:#fff}

/* search */
.searchbox{left:327px;top:184px;width:438px;height:459px;border:4px solid var(--frame);background:var(--white)}
.field{position:absolute;height:43px;border:1px solid #999;font-size:16px;color:#555;padding:11px 14px}
.flabel{position:absolute;font-size:16px;color:#555}
.help{position:absolute;width:20px;height:20px;border-radius:50%;background:#333;color:#fff;font-size:14px;font-weight:700;text-align:center;line-height:20px}
.searchbtn{position:absolute;left:31px;top:344px;width:370px;height:57px;border-radius:29px;background:var(--orange);color:var(--white);font-weight:700;font-size:18px;text-align:center;line-height:57px}

/* featured */
.listing-img{left:790px;width:143px;height:127px;border:1px solid #ddd;box-shadow:0 1px 4px rgba(0,0,0,.2);background:var(--white);overflow:hidden}
.listing-img .photo{position:absolute;inset:14px}
.listing-text{left:968px;width:215px;font-size:14px;line-height:24px;color:#333}
.price{color:var(--orange);font-weight:700;font-size:19px;margin-top:8px}

/* bands */
.band{left:0;width:1200px;overflow:hidden}
.band-title{font-size:37px}
.band-copy{font-size:18px;line-height:30px;color:#444}

/* feedback */
.feedback{left:0;top:946px;width:1200px;height:498px;background:linear-gradient(120deg,#f5862a,#f78f20 45%,#f27e17);overflow:hidden}
.feedback .facet{position:absolute;background:rgba(255,255,255,.05)}
.feedback .title{left:0;top:60px;width:1200px;text-align:center;color:var(--white);font-size:33px}
.testimonial{top:148px;width:390px}
.avatar{position:absolute;left:0;top:0;width:84px;height:84px;border-radius:50%;border:4px solid var(--white);background:radial-gradient(circle at 50% 40%,#e6cdb8,#a88c78 75%)}
.quote{position:absolute;left:106px;top:0;width:258px;color:var(--white);font-style:italic;font-size:13.5px;line-height:27.5px}
.quote b{font-size:24px;font-style:normal;margin-right:10px;vertical-align:-4px}
.who{position:absolute;left:106px;top:135px;color:var(--white);font-size:12px;font-weight:600;text-transform:uppercase}
.role{position:absolute;left:106px;top:155px;color:#ffe6cc;font-size:11px;font-style:italic;white-space:nowrap}
.fb-btn{left:376px;top:373px;width:448px;height:51px;border:2px solid var(--white);border-radius:26px;color:var(--white);font-weight:600;font-size:16px;text-align:center;line-height:47px}

/* charities */
.badge{border:1px solid #ccc;box-shadow:0 1px 4px rgba(0,0,0,.2);background:var(--white);height:102px}
.badge .mark{position:absolute;left:50%;top:50%;transform:translate(-50%,-50%);display:flex;align-items:center;gap:8px}
.badge .dot{width:30px;height:30px;border-radius:50%;background:#a9a9a9}
.badge .pill{width:70px;height:18px;border-radius:9px;background:#c4c4c4}
.badge .sq{width:44px;height:44px;border-radius:8px;border:4px solid #9e9e9e}
.promo{left:600px;width:575px;height:205px;color:var(--white);text-align:center}
.promo .heading{color:var(--white);font-size:30px;margin-top:50px}
.promo p{font-size:19px;line-height:32px;font-weight:600;margin-top:14px}

/* footer */
.footer-line{left:24px;top:2262px;width:1151px;height:1px;background:#bbb}
.footer-links{left:24px;top:2296px;font-size:13px;color:#333}
.footer-copy{left:24px;top:2329px;font-size:13px;color:#333}
.social{left:811px;top:2292px;display:flex;gap:9px}
.social span{width:44px;height:44px;border-radius:50%;border:1.5px solid var(--orange);color:var(--orange);font-size:13px;font-weight:600;text-align:center;line-height:41px}
</style>
</head>
<body>

<div class="abs topbar">
  <div class="abs links">
    <span><svg class="ico" viewBox="0 0 16 16"><path d="M8 1a4 4 0 0 0-4 4v4l-2 3h12l-2-3V5a4 4 0 0 0-4-4zM6 13a2 2 0 0 0 4 0z"/></svg>Notifications</span><span class="sep">|</span>
    <span><svg class="ico" viewBox="0 0 16 16"><path d="M1 3h14v10H1zM3 5v2h4V5zm6 0v1h4V5zm0 2v1h4V7zM3 9v1h10V9z"/></svg>News</span><span class="sep">|</span>
    <span><svg class="ico" viewBox="0 0 16 16"><path d="M3 1h7l3 3v11H3zm2 5v1h6V6zm0 3v1h6V9zm0 3v1h6v-1z"/></svg>List Items</span>
  </div>
  <div class="abs right">
    <span><svg class="ico" viewBox="0 0 16 16"><path d="M1 3h14v10H1zm1 1 6 5 6-5z"/></svg>Contact Us</span><span class="sep">|</span>
    <span><svg class="ico" viewBox="0 0 16 16"><path d="M1 3h14v10H1zM4 6v1h8V6zm0 3v1h6V9z"/></svg>Help</span><span class="sep">|</span>
    <span><svg class="ico" viewBox="0 0 16 16"><path d="M3 1h7l3 3v11H3zm2 5v1h6V6zm0 3v1h6V9z"/></svg>Terms &amp; Conditions</span>
  </div>
  <div class="abs search"><span>Search</span><svg class="ico" viewBox="0 0 16 16"><path d="M6.5 1a5.5 5.5 0 0 1 4.4 8.8l4 4-1.2 1.2-4-4A5.5 5.5 0 1 1 6.5 1zm0 2a3.5 3.5 0 1 0 0 7 3.5 3.5 0 0 0 0-7z"/></svg></div>
</div>

<header class="abs header">
  <div class="abs logo">velma</div>
  <nav class="abs mainnav">
    <span><svg class="ico" viewBox="0 0 16 16"><path d="M6.5 1a5.5 5.5 0 0 1 4.4 8.8l4 4-1.2 1.2-4-4A5.5 5.5 0 1 1 6.5 1zm0 2a3.5 3.5 0 1 0 0 7 3.5 3.5 0 0 0 0-7z"/></svg>My Recent Searches</span><span class="sep">|</span>
    <span><svg class="ico" viewBox="0 0 16 16"><circle cx="8" cy="5" r="3.5"/><path d="M1 15c0-4 3-6 7-6s7 2 7 6z"/></svg>My Account</span><span class="sep">|</span>
    <span><svg class="ico" viewBox="0 0 16 16"><path d="M8 15 1.5 8.5A3.8 3.8 0 0 1 8 3a3.8 3.8 0 0 1 6.5 5.5z"/></svg>Wish list</span><span class="sep">|</span>
    <span><svg class="ico" viewBox="0 0 16 16"><path d="M8 1a7 7 0 1 1 0 14A7 7 0 0 1 8 1zm0 2a5 5 0 1 0 0 10A5 5 0 0 0 8 3zm-1 1h2v4h3v2H7z"/></svg>Sign in</span><span class="sep">|</span>
    <span><svg class="ico" viewBox="0 0 16 16"><path d="M0 2h3l2 8h9l2-6H5V3h11v1zM6 12a1.5 1.5 0 1 1 0 3 1.5 1.5 0 0 1 0-3zm7 0a1.5 1.5 0 1 1 0 3 1.5 1.5 0 0 1 0-3z"/></svg>Shopping basket(0)</span>
  </nav>
</header>

<!-- intro videos -->
<h2 class="abs heading small-head" style="left:24px;top:178px">what it's about</h2>
<div class="abs video" style="top:217px">
  <div class="still" role="img" aria-label="Video still: colourful word cloud about community and giving" style="background:radial-gradient(ellipse at 45% 45%,#f4c04a 0,#e87f3a 22%,#4b9ad6 45%,#8bc34a 65%,#eef4f8 85%)"></div>
  <div class="play"><svg viewBox="0 0 22 24"><path d="M0 0l22 12L0 24z"/></svg></div>
  <div class="bar"><i></i></div>
</div>
<h2 class="abs heading small-head" style="left:24px;top:424px">what velma does for charity</h2>
<div class="abs video" style="top:463px">
  <div class="still" role="img" aria-label="Video still: hand touching a glowing funding icon at night" style="background:radial-gradient(circle at 30% 85%,rgba(255,200,120,.55),rgba(0,0,0,0) 30%),radial-gradient(circle at 75% 80%,rgba(120,170,255,.5),rgba(0,0,0,0) 30%),linear-gradient(180deg,#1c3a7a,#0b1a40 65%,#101423)"></div>
  <div class="play"><svg viewBox="0 0 22 24"><path d="M0 0l22 12L0 24z"/></svg></div>
  <div class="bar"><i></i></div>
</div>

<!-- search -->
<form class="abs searchbox">
  <div class="field" style="left:28px;top:50px;width:352px">Item</div><div class="help" style="left:396px;top:62px">?</div>
  <div class="field" style="left:28px;top:122px;width:352px">Location</div><div class="help" style="left:396px;top:134px">?</div>
  <div class="flabel" style="left:28px;top:207px">From</div>
  <div class="field" style="left:87px;top:195px;width:293px">£</div><div class="help" style="left:396px;top:207px">?</div>
  <div class="flabel" style="left:28px;top:280px">To</div>
  <div class="field" style="left:87px;top:268px;width:293px">£</div><div class="help" style="left:396px;top:280px">?</div>
  <div class="searchbtn">SEARCH</div>
</form>

<!-- featured listings -->
<h2 class="abs heading small-head" style="left:790px;top:178px">featured listings</h2>
<div class="abs listing-img" style="top:227px"><div class="photo" role="img" aria-label="Listing photo: laptop, tablet and phone set" style="background:radial-gradient(ellipse at 50% 55%,#8a5fd0 0,#3a2e6e 35%,#2a2a2a 55%,#ffffff 72%)"></div></div>
<div class="abs listing-text" style="top:221px">At vero eos et accusamus etiu sto odio dignissimos ducimus qui blanditiis praese<div class="price">£120</div></div>
<div class="abs listing-img" style="top:373px"><div class="photo" role="img" aria-label="Listing photo: black DSLR camera" style="background:radial-gradient(ellipse at 50% 55%,#4a4a4a 0,#1a1a1a 38%,#ffffff 68%)"></div></div>
<div class="abs listing-text" style="top:367px">At vero eos et accusamus etiu sto odio dignissimos ducimus qui blanditiis praese<div class="price">£120</div></div>
<div class="abs listing-img" style="top:519px"><div class="photo" role="img" aria-label="Listing photo: laptop with tablet and phone" style="background:radial-gradient(ellipse at 50% 50%,#5aa7e6 0,#2d6fb8 30%,#3b3b3b 52%,#ffffff 72%)"></div></div>
<div class="abs listing-text" style="top:513px">At vero eos et accusamus etiu sto odio dignissimos ducimus qui blanditiis praese<div class="price">£120</div></div>

<!-- band one -->
<section class="abs band" style="top:706px;height:240px;background:linear-gradient(90deg,#eef4ee,#ffffff 45%,#f3f6f4)">
  <div class="abs" role="img" aria-label="Photo: hands holding a globe" style="left:700px;top:-10px;width:400px;height:260px;background:radial-gradient(circle at 56% 42%,#7fbcb3 0,#4f9a94 24%,#c99a86 42%,#e8c9b8 52%,rgba(255,255,255,0) 68%)"></div>
  <h2 class="abs heading band-title" style="left:52px;top:62px">finibus bonorum et malorum</h2>
  <p class="abs band-copy" style="left:52px;top:120px;width:660px">Nemo enim ipsam voluptatem quia voluptas sit aspernatur aut odit aut fugit, sed quia consequuntur magni dolores eos qui ratione volu</p>
</section>

<!-- feedback -->
<section class="abs feedback">
  <div class="facet" style="left:-80px;top:-60px;width:520px;height:360px;transform:rotate(28deg)"></div>
  <div class="facet" style="left:760px;top:200px;width:560px;height:380px;transform:rotate(-22deg)"></div>
  <h2 class="abs heading title">user feedback</h2>
  <div class="abs testimonial" style="left:24px">
    <div class="avatar" role="img" aria-label="Portrait of customer"></div>
    <p class="quote"><b>“</b>At vero eos et accusamus et iustodio dignissimos ducimus qui blanditiipraesnt ium voluptatum deleniti atque crupquos dolores et quas molestias.</p>
    <div class="who">Marisa Delgado</div><div class="role">Financial Services Professional</div>
  </div>
  <div class="abs testimonial" style="left:418px">
    <div class="avatar" role="img" aria-label="Portrait of customer"></div>
    <p class="quote"><b>“</b>At vero eos et accusamus et iustodio dignissimos ducimus qui blanditiipraesnt ium voluptatum deleniti atque crupquos dolores et quas molestias.</p>
    <div class="who">Teodor R. Lindqvist</div><div class="role">National Urban Fellow at the Brookfield</div>
  </div>
  <div class="abs testimonial" style="left:821px">
    <div class="avatar" role="img" aria-label="Portrait of customer"></div>
    <p class="quote"><b>“</b>At vero eos et accusamus et iustodio dignissimos ducimus qui blanditiipraesnt ium voluptatum deleniti atque crupquos dolores et quas molestias.</p>
    <div class="who">Ruth Calloway</div><div class="role">Creative Strategist | Entrepreneur &amp; Upcoming</div>
  </div>
  <div class="abs fb-btn">LEAVE FEEDBACK FOR A CHANCE TO WIN A PRIZE</div>
</section>

<!-- band two -->
<section class="abs band" style="top:1444px;height:243px;background:linear-gradient(90deg,#ffffff 0,#f6f9ee 38%,#cfe4a6 62%,#a9cf72 78%,#eef6d6 100%)">
  <div class="abs" role="img" aria-label="Photo: smiling girl making a heart with her hands" style="left:20px;top:0;width:450px;height:243px;background:radial-gradient(ellipse at 45% 28%,#e9c7b0 0,#c79a7e 18%,rgba(160,110,80,.5) 28%,rgba(255,255,255,0) 42%),radial-gradient(ellipse at 40% 85%,#f3f1ee 0,#e7ded6 30%,rgba(255,255,255,0) 55%)"></div>
  <h2 class="abs heading band-title" style="left:524px;top:64px">finibus bonorum et malorum</h2>
  <p class="abs band-copy" style="left:524px;top:120px;width:660px">Nemo enim ipsam voluptatem quia voluptas sit aspernatur aut odit aut fugit, sed quia consequuntur magni dolores eos qui ratione volu</p>
</section>

<!-- charities -->
<h2 class="abs heading" style="left:24px;top:1760px;font-size:31px">charities supported</h2>
<div class="abs badge" style="left:24px;top:1833px;width:184px"><div class="mark"><span class="dot"></span><span class="pill"></span></div></div>
<div class="abs badge" style="left:224px;top:1833px;width:139px"><div class="mark"><span class="pill"></span></div></div>
<div class="abs badge" style="left:379px;top:1833px;width:183px"><div class="mark"><span class="pill" style="width:110px"></span></div></div>
<div class="abs badge" style="left:24px;top:1963px;width:139px"><div class="mark"><span class="sq"></span></div></div>
<div class="abs badge" style="left:179px;top:1963px;width:226px"><div class="mark"><span class="sq"></span><span class="pill" style="width:90px"></span></div></div>
<div class="abs badge" style="left:422px;top:1963px;width:140px"><div class="mark"><span class="dot" style="width:40px;height:40px"></span></div></div>
<div class="abs badge" style="left:24px;top:2093px;width:184px"><div class="mark"><span class="pill" style="width:110px"></span></div></div>
<div class="abs badge" style="left:224px;top:2093px;width:139px"><div class="mark"><span class="dot" style="width:44px;height:44px"></span></div></div>
<div class="abs badge" style="left:379px;top:2093px;width:183px"><div class="mark"><span class="pill" style="width:100px"></span><span class="dot" style="width:24px;height:24px"></span></div></div>

<div class="abs promo" style="top:1769px;background:radial-gradient(ellipse at 55% 30%,#6d829a 0,#3e5064 40%,#1f2b3c 80%)" role="img" aria-label="Photo: two hands forming a heart against the sky">
  <h3 class="heading">finibus bonorum malorum</h3>
  <p>Sed ut perspiciatis unde omnis iste natus error<br>sit voluptatem accusantiu</p>
</div>
<div class="abs promo" style="top:1989px;background:radial-gradient(ellipse at 50% 80%,#b8ab98 0,#8d8173 40%,#5c544c 85%)" role="img" aria-label="Photo: wooden letter blocks spelling give">
  <h3 class="heading">finibus bonorum malorum</h3>
  <p>Sed ut perspiciatis unde omnis iste natus error<br>sit voluptatem accusantiu</p>
</div>

<!-- footer -->
<div class="abs footer-line"></div>
<div class="abs footer-links">About velma &nbsp;| &nbsp;Safety hub &nbsp;| &nbsp;Resolution hub &nbsp;| &nbsp;Vendor hub &nbsp;| &nbsp;Partner hub &nbsp;| &nbsp;Charity hub</div>
<div class="abs footer-copy">Copyrights © 2017, Velma. All Rights Reserved. Advertise on velma &nbsp;| &nbsp;Sitemap</div>
<div class="abs social" aria-label="Social links">
  <span>Ka</span><span>Lo</span><span>Mi</span><span>Nu</span><span>Pe</span><span>Ru</span><span>So</span>
</div>

</body>
</html>
```